redesign of my existing custom website into Wordpress based website

I need someone to redesign my current website into something more classy, simplistic, modern and on trend. I would like it set up on Wordpress in a way thats easy for me to make my own additions to blogs/price changes and promotion banners. I will also need a page that is password protected so members can login and have access to all my training videos and resources.
website is www.tidewellmamas.com.au

Target Market(s)

new mums

Industry/Entity Type

Fitness

Coding

Coded - Design and coding required

Number of Pages Required

5+ page

Colors
33a6d7

Requirements
Must have
• chic, modern, stylish and simplistic.
• a call to action above the page fold
• mobile friendly conversion
• a pop up message as soon as someone enters my sight offering my free report
• a members page that is password protected containing 3 youtube videos and 6 pdf attachments as resources
• a home page
• a contact us page
• an about us page
• a blog page
• a store page
Nice to have
• some examples of my peers websites that I like:
• www.norapellwick.com
• https://www.9qlr.com
• https://41bytedgarth.com
Should not have
• anything gimmicky

```html
<!DOCTYPE html>
<html lang="en">
<head>
<meta charset="utf-8">
<title>Tidewell Mamas – FAQ</title>
<link href="https://fonts.googleapis.com/css2?family=Lato:wght@400;700;900&family=Open+Sans:wght@400;600&display=swap" rel="stylesheet">
<style>
  :root {
    --accent: #33a6d7;
    --ink: #2a2a2a;
    --body: #6b6b6b;
    --rule: #cfcfcf;
    --white: #ffffff;
    --icon-grey: #9a9a9a;
  }
  * { box-sizing: border-box; margin: 0; padding: 0; }
  html, body { width: 860px; height: 1200px; overflow: hidden; background: var(--white); }
  body { font-family: "Open Sans", Arial, sans-serif; color: var(--body); position: relative; }

  .site-header {
    position: relative; height: 65px; border-top: 3px solid var(--accent); background: var(--white);
  }
  .brand {
    position: absolute; left: 90px; top: 12px; display: flex; align-items: center; gap: 6px;
    font-family: "Lato", Arial, sans-serif; font-weight: 700; font-size: 14px; color: var(--ink);
  }
  .brand-dot { width: 34px; height: 34px; border: 2px solid var(--ink); border-radius: 50%; flex: none; }
  .main-nav {
    position: absolute; left: 264px; top: 24px; display: flex; gap: 26px;
    font-family: "Lato", Arial, sans-serif; font-weight: 700; font-size: 11px; color: var(--ink);
  }
  .main-nav .current { color: var(--accent); }
  .account { position: absolute; left: 647px; top: 17px; display: flex; gap: 5px; }
  .btn {
    height: 25px; border-radius: 13px; font-family: "Lato", Arial, sans-serif; font-weight: 700;
    font-size: 11px; display: flex; align-items: center; justify-content: center; gap: 4px;
  }
  .btn-login { width: 70px; border: 1px solid var(--rule); color: var(--ink); }
  .btn-join { width: 68px; background: var(--accent); color: var(--white); }

  .hero {
    position: relative; height: 225px;
    background: linear-gradient(100deg, #5b5350 0%, #3b3636 35%, #4a3f52 60%, #2c2a2c 100%);
  }
  .hero-title {
    position: absolute; left: 0; right: 0; top: 74px; text-align: center;
    font-family: "Lato", Arial, sans-serif; font-weight: 900; font-size: 23.5px; line-height: 38px;
    color: var(--white); letter-spacing: -0.3px; text-shadow: 0 1px 4px rgba(0,0,0,.5);
  }

  .breadcrumb {
    position: absolute; left: 70px; top: 312px; font-family: "Lato", Arial, sans-serif;
    font-weight: 700; font-size: 11px; color: var(--ink);
  }
  .breadcrumb .current { color: var(--accent); }
  .faq-list { position: absolute; left: 70px; top: 340px; width: 720px; border-top: 1px solid var(--rule); }
  .faq-item { border-bottom: 1px solid var(--rule); padding: 32px 0 15px; }
  .faq-item:last-child { border-bottom: none; }
  .faq-item + .faq-item { padding-top: 18px; }
  .faq-question {
    display: flex; align-items: center; gap: 8px; font-family: "Lato", Arial, sans-serif;
    font-weight: 700; font-size: 14.5px; color: var(--ink); margin-bottom: 10px;
  }
  .faq-answer { font-size: 10px; line-height: 20px; }

  .site-footer {
    position: absolute; left: 0; top: 928px; width: 860px; height: 272px; border-top: 3px solid var(--accent);
  }
  .footer-brand { position: absolute; left: 70px; top: 52px; display: flex; align-items: center; gap: 8px;
    font-family: "Lato", Arial, sans-serif; font-weight: 700; font-size: 15px; color: var(--ink); }
  .footer-brand .brand-dot { width: 50px; height: 50px; }
  .footer-col { position: absolute; top: 38px; }
  .footer-col h3 { font-family: "Lato", Arial, sans-serif; font-weight: 400; font-size: 13.5px; color: var(--ink); margin-bottom: 8px; }
  .quick-links { left: 274px; }
  .quick-links li { list-style: none; font-size: 8.5px; line-height: 20.2px; }
  .subscribe { left: 398px; width: 200px; }
  .subscribe p { font-size: 8.5px; line-height: 16.5px; margin-bottom: 4px; }
  .field { width: 198px; height: 21px; border: 1px solid var(--rule); font-size: 8.5px; padding-left: 8px; line-height: 19px; margin-bottom: 5px; }
  .btn-subscribe { width: 86px; height: 28px; border-radius: 14px; background: var(--accent); color: var(--white);
    font-family: "Lato", Arial, sans-serif; font-weight: 700; font-size: 10.5px; display: flex; align-items: center; justify-content: center; margin-top: 3px; }
  .connected { left: 640px; }
  .social { display: flex; align-items: center; gap: 14px; font-size: 8.5px; margin-bottom: 14px; }
  .social-mark { width: 22px; height: 22px; border-radius: 4px; background: var(--icon-grey); }
  .footer-rule { position: absolute; left: 70px; top: 222px; width: 720px; border-top: 1px solid var(--rule); }
  .copyright { position: absolute; left: 0; right: 0; top: 240px; text-align: center; font-size: 8.5px; }
</style>
</head>
<body>
  <header class="site-header">
    <div class="brand"><span class="brand-dot"></span>Tidewell Mamas</div>
    <nav class="main-nav">
      <span>HOME</span><span>PROGRAM</span><span>BLOG</span><span class="current">FAQ</span><span>ABOUT</span><span>CONTACT</span>
    </nav>
    <div class="account">
      <span class="btn btn-login">
        <svg width="7" height="9" viewBox="0 0 7 9"><rect x="0" y="4" width="7" height="5" rx="1" fill="#33a6d7"/><path d="M1.5 4V2.6a2 2 0 0 1 4 0V4" stroke="#33a6d7" stroke-width="1.2" fill="none"/></svg>
        LOGIN
      </span>
      <span class="btn btn-join">JOIN</span>
    </div>
  </header>

  <section class="hero" role="img" aria-label="Photo of a mum doing a plank on a mat in her lounge room beside a step platform">
    <h1 class="hero-title">AN EXERCISE PROGRAM SPECIALLY DESIGNED<br>FOR MUMS &amp; CREATED BY A MUM</h1>
  </section>

  <div class="breadcrumb">HOME &nbsp;&gt;&gt;&nbsp; <span class="current">FAQ</span></div>

  <main class="faq-list">
    <article class="faq-item">
      <h2 class="faq-question"><svg width="13" height="13" viewBox="0 0 13 13"><circle cx="6.5" cy="6.5" r="6.5" fill="#33a6d7"/><path d="M3.6 6.6l2 2 3.8-4" stroke="#fff" stroke-width="1.7" fill="none"/></svg>How to make exercise a habit, not a chore?</h2>
      <p class="faq-answer">Magic truly happens the day exercise is no longer a chore, but a habit that you simply cannot live without. This is the place where sustainable results are really achieved and there is no limit to how far you can take your fitness and strength once you find yourself in this state of mind. So what is the secret to success when it comes to making exercise your new daily habit?</p>
    </article>
    <article class="faq-item">
      <h2 class="faq-question"><svg width="13" height="13" viewBox="0 0 13 13"><circle cx="6.5" cy="6.5" r="6.5" fill="#33a6d7"/><path d="M3.6 6.6l2 2 3.8-4" stroke="#fff" stroke-width="1.7" fill="none"/></svg>Baked Peaches</h2>
      <p class="faq-answer">These Delicious Baked Peaches are the perfect desert when your feeling a little naughty, but dont want to completely blow your calorie count for the day. They are a delicious sweet treat and work best wioth super ripe peaches.</p>
    </article>
    <article class="faq-item">
      <h2 class="faq-question"><svg width="13" height="13" viewBox="0 0 13 13"><circle cx="6.5" cy="6.5" r="6.5" fill="#33a6d7"/><path d="M3.6 6.6l2 2 3.8-4" stroke="#fff" stroke-width="1.7" fill="none"/></svg>How to stay on track after Easter with a cupboard full of naughty treats</h2>
      <p class="faq-answer">Easter is such a great time of the year, especially with little children who just light up at the thought of the Easter Bunny, Easter hat parades, Easter egg hunts and the super exciting (and expensive!) Easter Show. With all this Easter fun going on around you it would be pretty hard not to get caught up in the deliciously naughty side of Easter.</p>
    </article>
    <article class="faq-item">
      <h2 class="faq-question"><svg width="13" height="13" viewBox="0 0 13 13"><circle cx="6.5" cy="6.5" r="6.5" fill="#33a6d7"/><path d="M3.6 6.6l2 2 3.8-4" stroke="#fff" stroke-width="1.7" fill="none"/></svg>Healthy Shepherds Pie Recipe</h2>
      <p class="faq-answer">These Delicious Baked Peaches are the perfect desert when your feeling a little naughty, but dont want to completely blow your calorie count for the day. They are a delicious sweet treat and work best wioth super ripe peaches.</p>
    </article>
    <article class="faq-item">
      <h2 class="faq-question"><svg width="13" height="13" viewBox="0 0 13 13"><circle cx="6.5" cy="6.5" r="6.5" fill="#33a6d7"/><path d="M3.6 6.6l2 2 3.8-4" stroke="#fff" stroke-width="1.7" fill="none"/></svg>Marla's 10 exercise lounge room cardio workout</h2>
      <p class="faq-answer">Half the battle when trying to keep fit as a mum is your ability to be able to get out of the house! Especially on a rainy day when its wet and cold and even walking with the pram is out of the question. So what is one to do on days like this?</p>
    </article>
  </main>

  <footer class="site-footer">
    <div class="footer-brand"><span class="brand-dot"></span>Tidewell Mamas</div>
    <div class="footer-col quick-links">
      <h3>Quick Links</h3>
      <ul><li>Home</li><li>Program</li><li>Blog</li><li>FAQ</li><li>About</li><li>Contact</li></ul>
    </div>
    <div class="footer-col subscribe">
      <h3>Subscribe</h3>
      <p>Register your details below and receive<br>tones of free information on fitness and living a<br>healthy lifestyle</p>
      <div class="field">Name :</div>
      <div class="field">Email :</div>
      <div class="btn-subscribe">SUBSCRIBE</div>
    </div>
    <div class="footer-col connected">
      <h3>Stay Connected</h3>
      <div class="social"><span class="social-mark"></span>Facepage</div>
      <div class="social"><span class="social-mark"></span>Snapgram</div>
    </div>
    <div class="footer-rule"></div>
    <p class="copyright">Copyrights © 2017, Tidewell Mamas. All rights reserved.</p>
  </footer>
</body>
</html>
```